Corporate Business Card

Very professional, Modern, Not to busy, include phone address email, website
(253) 617-4930, 18761 52nd Avenue S, Kent, WA 98047, martin@plumlinegroup.com, varkoworks.com

Target Market(s)

Manufacturing

Industry/Entity Type

Aero, machining, manufacturing, Off road racing

Contact Information for Business Card

Phone, address email, website

```html
<!DOCTYPE html>
<html lang="en">
<head>
<meta charset="utf-8">
<title>Varko Works – Business Card</title>
<link href="https://fonts.googleapis.com/css2?family=Exo+2:wght@500;600;700&family=Montserrat:wght@400;500&display=swap" rel="stylesheet">
<style>
  :root {
    --navy: #1f3368;
    --red: #d21f26;
    --white: #ffffff;
    --ink: #2b2b2b;
    --stage: #2e2e30;
  }
  * { margin: 0; padding: 0; box-sizing: border-box; }
  html, body { width: 1200px; height: 1186px; overflow: hidden; }
  body {
    background: var(--stage);
    position: relative;
    font-family: "Montserrat", sans-serif;
  }
  .card {
    position: absolute;
    left: 180px;
    width: 840px;
    height: 480px;
    border-radius: 26px;
    border-bottom: 6px solid var(--red);
    overflow: hidden;
  }
  .card--back { top: 70px; background: var(--navy); }
  .card--front { top: 620px; background: var(--white); }

  .wordmark {
    position: absolute;
    font-family: "Exo 2", sans-serif;
    font-weight: 700;
    font-size: 96px;
    letter-spacing: 1px;
    line-height: 1;
    white-space: nowrap;
  }
  .card--back .wordmark { left: 140px; top: 150px; color: var(--white); }
  .card--front .wordmark { left: 140px; top: 110px; color: var(--navy); }

  .rule {
    position: absolute;
    height: 3px;
    width: 330px;
  }
  .card--back .rule { left: 150px; top: 300px; background: var(--white); }
  .card--front .rule { left: 150px; top: 250px; background: var(--navy); }

  .holder {
    position: absolute;
    left: 150px;
    top: 296px;
    color: var(--ink);
  }
  .holder__name {
    font-family: "Exo 2", sans-serif;
    font-weight: 600;
    font-size: 36px;
    color: var(--red);
    line-height: 1.1;
  }
  .holder__role, .holder__address {
    font-size: 16px;
    line-height: 1.5;
  }

  .divider {
    position: absolute;
    left: 500px;
    top: 290px;
    width: 2px;
    height: 104px;
    background: var(--red);
  }

  .contact {
    position: absolute;
    left: 528px;
    top: 298px;
    list-style: none;
    font-size: 16px;
    color: var(--ink);
  }
  .contact li {
    display: flex;
    align-items: center;
    gap: 10px;
    line-height: 30px;
  }
  .contact svg { width: 15px; height: 15px; fill: var(--red); flex: none; }
</style>
</head>
<body>

  <section class="card card--back" aria-label="Card back">
    <div class="wordmark">Varko Works</div>
    <div class="rule"></div>
  </section>

  <section class="card card--front" aria-label="Card front">
    <div class="wordmark">Varko Works</div>
    <div class="rule"></div>

    <div class="holder">
      <p class="holder__name">Martin Keller</p>
      <p class="holder__role">Managing Director</p>
      <p class="holder__address">18761 52nd Avenue S, Kent, WA 98047</p>
    </div>

    <div class="divider"></div>

    <ul class="contact">
      <li>
        <svg viewBox="0 0 16 16" aria-hidden="true"><path d="M2 5c0-2 2-3 6-3s6 1 6 3v1h-3V5H5v1H2zM3 8h10l1 6H2z"/></svg>
        (253) 617-4930
      </li>
      <li>
        <svg viewBox="0 0 16 16" aria-hidden="true"><path d="M1 3h14v10H1zM2 4l6 5 6-5z" fill-rule="evenodd"/></svg>
        martin@plumlinegroup.com
      </li>
      <li>
        <svg viewBox="0 0 16 16" aria-hidden="true"><circle cx="8" cy="8" r="7"/></svg>
        www.varkoworks.com
      </li>
    </ul>
  </section>

</body>
</html>
```